WTF!!! We need a modern professional website for a business litigation law firm.

We need a modern, clean, professional and uncomplicated website for a new business trial and litigation law firm called "Haverlock Trial Firm PLLC". Website must be mobile optimized for iPad and smartphone. The law firm specializes in counseling and representing large corporations, small businesses and entrepreneurs in and out of the courtroom. Lawyers in the firm serve as Florida counsel and trial counsel to organizations facing claims involving product liability, premises liability, professional liability, vehicle and transportation liability, warranty claims, construction defects and delay claims, complex business disputes, commercial litigation and bid disputes in State and Federal Courts. The website is mainly to provide information about the firm, and should include sections describing the firm, identifying the Industries Served and Areas of Practice ," a separate page identifying the "Professionals", a separate page for "Resources & Advisories," and a traveling "Connect With Us" button a site visitor can click on that will launch an email to the Firm's general email account. The website should allow us to easily modify the content on these pages, and let us add/modify links to external information sources. We will not sell anything or take payments through the website. We do need to be able to easily upload and update photographs of attorneys and add new attorneys names/email hyperlinks as the firm grows. We would like to add developments in the law or success stories easily and quickly, such as through a blog page. On the "Connect With Us" page the website should have hyperlinks to email the Firm, and there should be hyperlinks to email each professional on the "Professionals" page. The website should be viewable on mobile devices without distortion. The law firm focuses on trial work and should have some imagery associated with courtrooms, but the overall theme of the site should be modern, clean, and communicate sophistication and strength. The website should be made in Wordpress. We have uploaded logo files for Haverlock Trial Firm.

Target Market(s)

Corporations and companies that are looking for legal representation. Other attorneys/legal industry.

Industry/Entity Type

Legal Industry

Coding

Coded - Design and coding required

Number of Pages Required

1 page

Font styles to use
Sans Serif

Requirements
Must have
• Simple, clean, sophisticated, modern website that includes the logo, watermark of logo, and the elements described above.
Nice to have
• Pictures of city scape, buildings, courtroom, team members.

```html
<!DOCTYPE html>
<html lang="en">
<head>
<meta charset="utf-8">
<title>Haverlock Trial Firm</title>
<link href="https://fonts.googleapis.com/css2?family=Anton&family=Open+Sans:wght@400;600;700;800&display=swap" rel="stylesheet">
<style>
:root{
  --accent:#b24a2c;
  --accent-dark:#8f3a22;
  --ink:#161616;
  --text:#444;
  --muted:#f3f3f3;
  --line:#e3e3e3;
  --white:#fff;
  --star:#f5b400;
}
*{box-sizing:border-box;margin:0;padding:0}
html,body{width:1200px;height:4874px;overflow:hidden}
body{font-family:"Open Sans",sans-serif;color:var(--text);background:var(--white);position:relative}
.abs{position:absolute}
.display{font-family:"Anton",sans-serif;font-weight:400;color:var(--ink);text-transform:uppercase;letter-spacing:.3px}
.display em{font-style:normal;color:var(--accent)}
.section-title{position:absolute;left:0;width:1200px;text-align:center;font-size:48px;line-height:1}
.body-copy{font-size:14.5px;line-height:28px;color:var(--text)}
.body-copy p+p{margin-top:14px}
.btn{position:absolute;background:var(--accent);color:var(--white);font-weight:700;font-size:14px;letter-spacing:.5px;text-transform:uppercase;display:flex;align-items:center;justify-content:center;box-shadow:0 5px 8px rgba(0,0,0,.18)}
.photo{position:absolute}
.shadow-box{position:absolute;background:#d6d6d6}
.arrow{position:absolute;width:42px;height:42px;border-radius:50%;background:var(--white);box-shadow:0 2px 8px rgba(0,0,0,.18);display:flex;align-items:center;justify-content:center}
.card{position:absolute;background:var(--white);border:1px solid var(--line);box-shadow:0 2px 6px rgba(0,0,0,.06)}
.card .label{position:absolute;left:0;right:0;bottom:0;text-align:center;font-size:15px;font-weight:600;color:var(--ink)}

.topbar{left:568px;top:0;width:632px;height:38px;background:var(--ink);clip-path:polygon(24px 0,100% 0,100% 100%,0 100%)}
.topbar-slash{left:560px;top:0;width:44px;height:38px;background:var(--accent);clip-path:polygon(0 0,26px 0,44px 38px,18px 38px)}
.topbar span{position:absolute;top:10px;color:var(--white);font-size:14px;display:flex;align-items:center;gap:8px}
.brand{position:absolute;left:112px;top:28px;color:var(--ink);font-weight:800;font-size:22px;line-height:24px;letter-spacing:.5px}
.nav{position:absolute;top:66px;left:341px;display:flex;gap:22px;font-size:14px;color:#555}
.nav .active{color:var(--ink);font-weight:600;border-bottom:2px solid var(--accent)}

.hero{left:0;top:115px;width:1200px;height:472px;background:linear-gradient(180deg,#8a6a55 0%,#a57b57 45%,#6f5a3c 75%,#2f3a25 100%)}
.hero-shade{left:0;top:115px;width:1200px;height:472px;background:linear-gradient(90deg,rgba(20,14,10,.55) 0%,rgba(20,14,10,.15) 55%,rgba(0,0,0,0) 100%)}
.hero-kicker{left:110px;top:188px;color:var(--white);font-size:40px;line-height:1}
.hero-title{left:110px;top:240px;color:var(--white);font-size:94px;line-height:94px}
.hero-rule{left:385px;top:474px;width:90px;height:2px;background:rgba(255,255,255,.6)}
</style>
</head>
<body>

<div class="abs topbar-slash"></div>
<div class="abs topbar">
  <span style="left:223px"><svg width="12" height="12" viewBox="0 0 24 24"><path fill="#fff" d="M6.6 10.8a15.1 15.1 0 0 0 6.6 6.6l2.2-2.2c.3-.3.7-.4 1-.2 1.1.4 2.3.6 3.6.6.6 0 1 .4 1 1V20c0 .6-.4 1-1 1C10.6 21 3 13.4 3 4c0-.6.4-1 1-1h3.5c.6 0 1 .4 1 1 0 1.3.2 2.5.6 3.6.1.3 0 .7-.2 1z"/></svg><b style="font-weight:600">+1555-010-2480</b></span>
  <span style="left:371px"><svg width="13" height="11" viewBox="0 0 24 20"><path fill="#fff" d="M0 2h24v16H0zM2 3l10 7 10-7"/></svg>info@haverlock.com</span>
</div>
<div class="brand">HAVERLOCK<br><span style="font-size:13px;letter-spacing:3px">TRIAL FIRM</span></div>
<nav class="nav">
  <span class="active">Home</span><span>About</span><span>Areas of Practice</span><span>Professionals</span><span>Resources &amp; Advisories</span><span>Blog</span>
</nav>
<div class="btn" style="left:954px;top:57px;width:136px;height:41px">Get Started</div>

<div class="abs hero" role="img" aria-label="City skyline of downtown office towers at sunset with palm trees"></div>
<div class="abs hero-shade"></div>
<div class="abs display hero-kicker">Haverlock Trial Firm</div>
<div class="abs display hero-title">Your Trial<br>Partner in<br>Justice</div>
<div class="abs hero-rule"></div>
<svg class="abs" style="left:44px;top:378px" width="20" height="30" viewBox="0 0 20 30"><path d="M16 2 4 15l12 13" stroke="#fff" stroke-width="2" fill="none"/></svg>
<svg class="abs" style="left:1146px;top:378px" width="20" height="30" viewBox="0 0 20 30"><path d="M4 2l12 13L4 28" stroke="#fff" stroke-width="2" fill="none"/></svg>

<div class="display section-title" style="top:665px">Our Firm<br><em>Your Advocates</em></div>
<div class="abs body-copy" style="left:113px;top:824px;width:505px">
  <p>Sed ut perspiciatis une omnis iste natus error sit vatem accusantium doloremque laudantium, totam rem aperiam, eaque ipsa quae ab illo inventore veritatis et quasi architecto beatae vitae cta sunt explicabo. Nemo enim ipsam voluptatem quia voluptas sit aspernatur aut odit aut fugit, sed quia consequuntur magni dolores</p>
  <p>Sed ut perspiciatis une omnis iste natus error sit vatem accusantium doloremque laudantium, totam rem aperiam, eaque ipsa quae ab illo inventore veritatis et quasi architecto beatae vitae cta sunt explicabo. Nemo enim ipsam voluptatem quia voluptas sit aspernatur aut odit</p>
</div>
<div class="btn" style="left:113px;top:1122px;width:193px;height:43px">Connect With Us</div>
<div class="shadow-box" style="left:661px;top:846px;width:413px;height:341px"></div>
<div class="photo" style="left:680px;top:824px;width:410px;height:340px;background:linear-gradient(135deg,#2f5a7a,#6d8fa8 50%,#b9c6cf)" role="img" aria-label="Two business professionals walking past glass office buildings"></div>

<div class="abs" style="left:0;top:1265px;width:1200px;height:543px;background:var(--muted)"></div>
<div class="display section-title" style="top:1346px">Our Areas of <em>Expertise</em></div>
<div class="card" style="left:112px;top:1438px;width:216px;height:275px"><div class="photo" style="left:0;top:0;width:214px;height:205px;background:linear-gradient(135deg,#1d4f86,#5c8fc0)" role="img" aria-label="Engineer inspecting equipment in a factory"></div><div class="label" style="height:70px;line-height:70px">Product Liability</div></div>
<div class="card" style="left:365px;top:1438px;width:216px;height:275px"><div class="photo" style="left:0;top:0;width:214px;height:205px;background:linear-gradient(180deg,#8c7d6b,#b9b3a8 60%,#6f6a60)" role="img" aria-label="Snowy sidewalk with a wet floor warning sign"></div><div class="label" style="height:70px;line-height:70px">Premises Liability</div></div>
<div class="card" style="left:619px;top:1438px;width:216px;height:275px"><div class="photo" style="left:0;top:0;width:214px;height:205px;background:linear-gradient(135deg,#2b2d31,#5a3b34 50%,#3a3c40)" role="img" aria-label="Damaged car after a road collision"></div><div class="label" style="height:70px;line-height:70px">Vehicle &amp; Transportation</div></div>
<div class="card" style="left:873px;top:1438px;width:216px;height:275px"><div class="photo" style="left:0;top:0;width:214px;height:205px;background:linear-gradient(135deg,#6a4a3a,#a8b7c4 60%,#3d5c7e)" role="img" aria-label="Hand signing a warranty document"></div><div class="label" style="height:70px;line-height:70px">Warranty Claims</div></div>
<div class="arrow" style="left:90px;top:1558px"><svg width="12" height="12" viewBox="0 0 12 12"><path d="M8 1 3 6l5 5" stroke="#222" stroke-width="1.6" fill="none"/></svg></div>
<div class="arrow" style="left:1071px;top:1558px"><svg width="12" height="12" viewBox="0 0 12 12"><path d="M4 1l5 5-5 5" stroke="#222" stroke-width="1.6" fill="none"/></svg></div>

<div class="display section-title" style="top:1938px">Resources &amp; <em>Advisories</em></div>
<div class="shadow-box" style="left:95px;top:2077px;width:411px;height:364px"></div>
<div class="photo" style="left:114px;top:2054px;width:410px;height:363px;background:linear-gradient(135deg,#c9a683,#7d6a5c 50%,#2e3d55)" role="img" aria-label="Advisor reviewing documents with an older couple"></div>
<div class="abs body-copy" style="left:585px;top:2081px;width:505px">
  <p>Sed ut perspiciatis une omnis iste natus error sit vatem accusantium doloremque laudantium, totam rem aperiam, eaque ipsa quae ab illo inventore veritatis et quasi architecto beatae vitae cta sunt explicabo. Nemo enim ipsam voluptatem quia voluptas sit aspernatur aut odit aut fugit, sed quia consequuntur magni dolores</p>
  <p>Sed ut perspiciatis une omnis iste natus error sit vatem accusantium doloremque laudantium, totam rem aperiam, eaque ipsa quae ab illo inventore veritatis et quasi architecto beatae vitae cta sunt explicabo. Nemo enim ipsam voluptatem quia voluptas sit aspernatur aut odit</p>
</div>
<div class="btn" style="left:585px;top:2387px;width:146px;height:42px">Learn More</div>

<div class="display section-title" style="top:2578px">Industries We <em>Serve</em></div>
<div class="card" style="left:112px;top:2671px;width:294px;height:275px"><div class="photo" style="left:0;top:0;width:292px;height:206px;background:linear-gradient(135deg,#e6e2dc,#8ea0b5 55%,#2f3a4c)" role="img" aria-label="Corporate colleagues reviewing work on a laptop"></div><div class="label" style="height:69px;line-height:69px">Large Corporations</div></div>
<div class="card" style="left:454px;top:2671px;width:295px;height:275px"><div class="photo" style="left:0;top:0;width:293px;height:206px;background:linear-gradient(135deg,#a57c56,#d8c3a5 55%,#6b4d35)" role="img" aria-label="Small business owner packing orders at a desk"></div><div class="label" style="height:69px;line-height:69px">Small Businesses</div></div>
<div class="card" style="left:797px;top:2671px;width:294px;height:275px"><div class="photo" style="left:0;top:0;width:292px;height:206px;background:linear-gradient(135deg,#3b4b63,#6f7f92 50%,#1d2026)" role="img" aria-label="Mechanic working on a vehicle engine"></div><div class="label" style="height:69px;line-height:69px">Transportation</div></div>
<div class="arrow" style="left:90px;top:2790px"><svg width="12" height="12" viewBox="0 0 12 12"><path d="M8 1 3 6l5 5" stroke="#222" stroke-width="1.6" fill="none"/></svg></div>
<div class="arrow" style="left:1071px;top:2790px"><svg width="12" height="12" viewBox="0 0 12 12"><path d="M4 1l5 5-5 5" stroke="#222" stroke-width="1.6" fill="none"/></svg></div>

<div class="abs" style="left:0;top:3034px;width:1200px;height:538px;background:var(--muted)"></div>
<div class="display section-title" style="top:3110px">Satisfied <em>Clients</em></div>
<div class="abs" style="left:159px;top:3195px;width:886px;height:292px;border-radius:6px;background:linear-gradient(120deg,#161313 0%,#2a1b16 45%,#6a3320 80%,#8c4229 100%)">
  <div class="abs" style="left:0;top:70px;width:886px;text-align:center;color:var(--star);font-size:22px;letter-spacing:2px">★★★★★</div>
  <div class="abs" style="left:60px;top:110px;width:766px;text-align:center;color:var(--white);font-style:italic;font-size:16.5px;line-height:26px">"Nemo enim ipsam voluptatem quia voluptas sit aspernatur aut odit aut fugit, sed quia consequuntur magni dolores eos qui ratione voluptatem sequi nesciunt. Neque porro quisquam est, qui ore et dolore magnam aliquam quaerat voluptatem."</div>
  <div class="abs" style="left:0;top:222px;width:886px;text-align:center;color:var(--white);font-size:17px">Marcus</div>
</div>
<div class="arrow" style="left:131px;top:3320px"><svg width="12" height="12" viewBox="0 0 12 12"><path d="M8 1 3 6l5 5" stroke="#222" stroke-width="1.6" fill="none"/></svg></div>
<div class="arrow" style="left:1028px;top:3320px"><svg width="12" height="12" viewBox="0 0 12 12"><path d="M4 1l5 5-5 5" stroke="#222" stroke-width="1.6" fill="none"/></svg></div>

<div class="display section-title" style="top:3658px">Get in <em>Touch</em></div>
<div class="abs body-copy" style="left:230px;top:3740px;width:740px;text-align:center">Acusantium doloremque laudantium, totam rem aperiam, eaque ipsa quae ab illo inventore veritatis et quasi architecto beatae vitae dicta sunt explicabo. Nemo enim ipsam voluptatem quia voluptas sit aspernatur aut odit aut fugit, sed quia consequuntur magni dolores eos qui ratione</div>
<div class="abs" style="left:0;top:3838px;width:1200px;text-align:center;font-size:15px;font-weight:600;color:var(--ink)">Nemo enim ipsam voluptatem quia voluptas!</div>
<div class="btn" style="left:473px;top:3890px;width:254px;height:42px">Connect With Us</div>

<div class="abs" style="left:0;top:4007px;width:1200px;height:536px;background:var(--muted)"></div>
<div class="display section-title" style="top:4088px">Fresh from <em>the Blog</em></div>
<div class="card" style="left:151px;top:4193px;width:440px;height:256px;border-bottom:9px solid var(--ink)">
  <div class="abs" style="left:20px;top:28px;font-size:21px;font-weight:600;color:var(--ink)">Finibus Bonorum et Malorum</div>
  <div class="abs" style="left:24px;top:66px;font-size:14px;color:var(--accent)">by jcarterlaw | Jan 20, 2025</div>
  <div class="abs body-copy" style="left:20px;top:102px;width:400px;font-size:14.5px">Lorem ipsum dolor sit amet, consectetur adipiscing elit, sed do eiusmod tempor incididunt ut labore et dolore magna aliqua. Ut enim ad minim veniam, quis nostrud exercitation por incididunt ut labor <b style="color:var(--accent);font-weight:600">MORE</b></div>
  <div class="abs" style="left:-1px;right:-1px;bottom:-9px;height:4px;background:var(--accent)"></div>
</div>
<div class="card" style="left:610px;top:4193px;width:440px;height:256px;border-bottom:9px solid var(--ink)">
  <div class="abs" style="left:20px;top:28px;font-size:21px;font-weight:600;color:var(--ink)">Finibus Bonorum et Malorum</div>
  <div class="abs" style="left:24px;top:66px;font-size:14px;color:var(--accent)">by jcarterlaw | Jan 20, 2025</div>
  <div class="abs body-copy" style="left:20px;top:102px;width:400px;font-size:14.5px">Lorem ipsum dolor sit amet, consectetur adipiscing elit, sed do eiusmod tempor incididunt ut labore et dolore magna aliqua. Ut enim ad minim veniam, quis nostrud exercitation por incididunt ut labor <b style="color:var(--accent);font-weight:600">MORE</b></div>
  <div class="abs" style="left:-1px;right:-1px;bottom:-9px;height:4px;background:var(--accent)"></div>
</div>
<div class="arrow" style="left:90px;top:4312px"><svg width="12" height="12" viewBox="0 0 12 12"><path d="M8 1 3 6l5 5" stroke="#222" stroke-width="1.6" fill="none"/></svg></div>
<div class="arrow" style="left:1071px;top:4312px"><svg width="12" height="12" viewBox="0 0 12 12"><path d="M4 1l5 5-5 5" stroke="#222" stroke-width="1.6" fill="none"/></svg></div>

<footer class="abs" style="left:0;top:4543px;width:1200px;height:331px;background:var(--ink)">
  <div class="abs" style="left:150px;top:100px;width:240px;text-align:center;color:var(--white);font-weight:800;font-size:32px;line-height:36px;letter-spacing:1px">HAVERLOCK<br><span style="font-size:18px;letter-spacing:5px">TRIAL FIRM</span></div>
  <div class="abs" style="left:113px;top:242px;color:var(--white);font-size:14px">2025 Haverlock Trial Firm. All Rights Reserved.</div>

  <div class="abs display" style="left:486px;top:84px;color:var(--white);font-size:20px">Contact</div>
  <svg class="abs" style="left:486px;top:130px" width="16" height="20" viewBox="0 0 16 20"><path fill="#fff" d="M8 0a7 7 0 0 0-7 7c0 5 7 13 7 13s7-8 7-13a7 7 0 0 0-7-7zm0 9.5A2.5 2.5 0 1 1 8 4.5a2.5 2.5 0 0 1 0 5z"/></svg>
  <div class="abs" style="left:527px;top:130px;color:var(--white);font-size:14.5px;line-height:25px">Haverlock Trial Firm,<br>Address comes here</div>
  <svg class="abs" style="left:487px;top:201px" width="14" height="14" viewBox="0 0 24 24"><path fill="#fff" d="M6.6 10.8a15.1 15.1 0 0 0 6.6 6.6l2.2-2.2c.3-.3.7-.4 1-.2 1.1.4 2.3.6 3.6.6.6 0 1 .4 1 1V20c0 .6-.4 1-1 1C10.6 21 3 13.4 3 4c0-.6.4-1 1-1h3.5c.6 0 1 .4 1 1 0 1.3.2 2.5.6 3.6.1.3 0 .7-.2 1z"/></svg>
  <div class="abs" style="left:527px;top:197px;color:var(--accent);font-size:16px;font-weight:600">+1555-010-2481</div>
  <svg class="abs" style="left:486px;top:239px" width="16" height="14" viewBox="0 0 16 14"><path fill="#fff" d="M4 0h8v3H4zM1 4h14v6h-3v4H4v-4H1zm4 5v3h6V9z"/></svg>
  <div class="abs" style="left:527px;top:236px;color:var(--white);font-size:14.5px">info@haverlock.com</div>

  <div class="abs display" style="left:768px;top:84px;color:var(--white);font-size:20px">Quick Links</div>
  <div class="abs" style="left:768px;top:125px;color:var(--white);font-size:14px;line-height:28px">About<br>Areas of Practice<br>Professionals</div>
  <div class="abs" style="left:933px;top:125px;color:var(--white);font-size:14px;line-height:28px">Resources &amp; Advisories<br>Blog<br>Contact Us</div>
  <div class="btn" style="left:763px;top:227px;width:202px;height:40px;font-size:15px">Connect With Us</div>
</footer>

</body>
</html>
```